Corporate Template

Looking for a set of corporate slides to be made which contain multiple different slides and orientations. Looking for at least 8 to 10 different master pages plus a Coversheet and closeout page. Incorporating a color palate similar to our logo coloring is preferred.
I have attached a logo.
I like the amber quill works designs best so far. They seem to fit what I'm looking for in terms of visual appearance.
Reason: I'm trying to allow time for a couple new designers to incorporate some changes I requested to their existing designs.

```html
<!DOCTYPE html>
<html lang="en">
<head>
<meta charset="utf-8">
<title>Helix Neuro-Diagnostics – Slide Masters</title>
<link href="https://fonts.googleapis.com/css2?family=Arimo:wght@400;700&display=swap" rel="stylesheet">
<style>
  :root{
    --canvas:#e3e3e3;
    --white:#ffffff;
    --sky:#3dc1ee;
    --cyan:#22dffa;
    --ice:#7ff6fd;
    --azure:#0aaaec;
    --bright:#18c6f6;
    --royal:#1a8ee0;
    --navy:#1a5fb0;
    --glow:#0f97f0;
    --ink:#2574c4;
    --mist:#c9ced3;
  }
  *{margin:0;padding:0;box-sizing:border-box}
  html,body{width:1200px;height:977px;overflow:hidden;background:var(--canvas)}
  body{position:relative;font-family:"Arimo",Arial,sans-serif;color:var(--white)}

  .slide{position:absolute;width:367px;height:274px;overflow:hidden;background:var(--white)}
  .slide svg.bg{position:absolute;inset:0;width:100%;height:100%}
  .col-1{left:28px}.col-2{left:420px}.col-3{left:800px}
  .row-1{top:27px}.row-2{top:326px}.row-3{top:620px}

  .brand{position:absolute;text-align:center;line-height:1}
  .brand .word{display:block;font-weight:400;font-size:38px;letter-spacing:1px}
  .brand .sub{display:block;font-weight:700;font-size:12.5px;margin-top:2px}
  .brand.cover{left:0;right:0;top:106px}
  .brand.blue{color:var(--ink)}
  .brand.mini .word{font-size:12px;letter-spacing:.5px}
  .brand.mini .sub{font-size:4.5px;margin-top:1px}
  .brand.faint{color:var(--mist)}

  .heading{position:absolute;left:0;right:0;text-align:center;font-weight:700;font-size:25px;line-height:1}
  .heading .subtitle{display:block;font-weight:400;font-size:12px;margin-top:5px}
  .heading.blue{color:var(--ink)}

  .thanks{position:absolute;left:0;right:0;text-align:center;font-weight:700;line-height:1}
  .thanks.big{font-size:30px}
  .thanks.wide{font-size:19.5px}
  .social{display:flex;justify-content:center;gap:5px;margin-top:14px}
  .social span{width:20px;height:20px;border-radius:50%;background:var(--white)}

  .contact{position:absolute;font-size:7px;line-height:1.75;font-style:normal}
  .contact .url{font-weight:700}
  .contact.right{text-align:right;line-height:1.35}
</style>
</head>
<body>

<!-- Cover: cyan X -->
<section class="slide col-1 row-1">
  <svg class="bg" viewBox="0 0 367 274" preserveAspectRatio="none" aria-hidden="true">
    <rect width="367" height="170" fill="var(--sky)"/>
    <rect y="169" width="367" height="105" fill="var(--azure)"/>
    <polygon points="32,0 335,0 183,205" fill="var(--cyan)" opacity=".85"/>
    <polygon points="129,274 239,274 184,200" fill="var(--royal)"/>
  </svg>
  <div class="brand cover"><span class="word">HELIX</span><span class="sub">NEURO-DIAGNOSTICS</span></div>
</section>

<!-- Divider: cyan X band -->
<section class="slide col-2 row-1">
  <svg class="bg" viewBox="0 0 367 274" preserveAspectRatio="none" aria-hidden="true">
    <rect y="51" width="367" height="79" fill="var(--sky)"/>
    <rect y="129" width="367" height="93" fill="var(--azure)"/>
    <polygon points="100,51 267,51 183,165" fill="var(--cyan)" opacity=".85"/>
    <polygon points="138,222 228,222 183,160" fill="var(--royal)"/>
  </svg>
  <h2 class="heading" style="top:106px">DIVIDER PAGE HERE<span class="subtitle">SUBTITLE HERE</span></h2>
  <div class="brand mini faint" style="right:10px;top:249px"><span class="word">HELIX</span><span class="sub">NEURO-DIAGNOSTICS</span></div>
</section>

<!-- Closeout: cyan X -->
<section class="slide col-3 row-1">
  <svg class="bg" viewBox="0 0 367 274" preserveAspectRatio="none" aria-hidden="true">
    <rect width="367" height="170" fill="var(--sky)"/>
    <rect y="169" width="367" height="105" fill="var(--azure)"/>
    <polygon points="32,0 335,0 183,205" fill="var(--cyan)" opacity=".85"/>
    <polygon points="129,274 239,274 184,200" fill="var(--royal)"/>
  </svg>
  <div class="thanks big" style="top:104px">THANKS
    <div class="social"><span></span><span></span><span></span><span></span><span></span></div>
  </div>
  <address class="contact" style="left:20px;top:220px">
    <div class="url">http://helixneuro.net/</div>
    <div>admin@helixneuro.com</div>
    <div>1480 Larkspur Lane, Cedar Hollow, TX 75112</div>
  </address>
  <div class="brand mini" style="right:22px;top:239px"><span class="word">HELIX</span><span class="sub">NEURO-DIAGNOSTICS</span></div>
</section>

<!-- Cover: deep blue diagonals -->
<section class="slide col-1 row-2">
  <svg class="bg" viewBox="0 0 367 274" preserveAspectRatio="none" aria-hidden="true">
    <defs>
      <radialGradient id="deep-a" cx="50%" cy="55%" r="65%"><stop offset="0" stop-color="var(--glow)"/><stop offset="1" stop-color="var(--navy)"/></radialGradient>
    </defs>
    <rect width="367" height="274" fill="var(--bright)"/>
    <polygon points="180,0 367,0 367,30 210,30" fill="var(--royal)"/>
    <polygon points="0,240 150,240 185,274 0,274" fill="var(--royal)"/>
    <rect y="32" width="367" height="208" fill="url(#deep-a)"/>
    <polygon points="0,170 0,240 70,240" fill="var(--bright)" opacity=".8"/>
    <polygon points="310,32 367,32 367,100" fill="var(--bright)" opacity=".8"/>
  </svg>
  <div class="brand cover"><span class="word">HELIX</span><span class="sub">NEURO-DIAGNOSTICS</span></div>
</section>

<!-- Divider: deep blue band -->
<section class="slide col-2 row-2">
  <svg class="bg" viewBox="0 0 367 274" preserveAspectRatio="none" aria-hidden="true">
    <defs>
      <radialGradient id="deep-b" cx="50%" cy="50%" r="70%"><stop offset="0" stop-color="var(--glow)"/><stop offset="1" stop-color="var(--navy)"/></radialGradient>
    </defs>
    <rect y="48" width="367" height="176" fill="var(--bright)"/>
    <polygon points="180,48 367,48 367,82 210,82" fill="var(--royal)"/>
    <polygon points="0,190 150,190 185,224 0,224" fill="var(--royal)"/>
    <rect y="82" width="367" height="108" fill="url(#deep-b)"/>
    <polygon points="0,130 0,190 55,190" fill="var(--bright)" opacity=".8"/>
    <polygon points="315,82 367,82 367,140" fill="var(--bright)" opacity=".8"/>
  </svg>
  <h2 class="heading" style="top:114px">DIVIDER PAGE HERE<span class="subtitle">SUBTITLE HERE</span></h2>
  <div class="brand mini faint" style="right:16px;top:246px"><span class="word">HELIX</span><span class="sub">NEURO-DIAGNOSTICS</span></div>
</section>

<!-- Closeout: deep blue diagonals -->
<section class="slide col-3 row-2">
  <svg class="bg" viewBox="0 0 367 274" preserveAspectRatio="none" aria-hidden="true">
    <defs>
      <radialGradient id="deep-c" cx="50%" cy="55%" r="65%"><stop offset="0" stop-color="var(--glow)"/><stop offset="1" stop-color="var(--navy)"/></radialGradient>
    </defs>
    <rect width="367" height="274" fill="var(--bright)"/>
    <polygon points="180,0 367,0 367,30 210,30" fill="var(--royal)"/>
    <polygon points="0,240 150,240 185,274 0,274" fill="var(--royal)"/>
    <rect y="32" width="367" height="208" fill="url(#deep-c)"/>
    <polygon points="0,170 0,240 70,240" fill="var(--bright)" opacity=".8"/>
    <polygon points="310,32 367,32 367,100" fill="var(--bright)" opacity=".8"/>
  </svg>
  <div class="thanks wide" style="top:120px">THANKS FOR WATCHING</div>
  <address class="contact right" style="right:24px;top:189px">
    <div class="url">http://helixneuro.net/</div>
    <div>admin@helixneuro.com</div>
    <div>1480 Larkspur Lane</div>
    <div>Cedar Hollow, TX 75112</div>
  </address>
  <div class="brand mini" style="right:22px;top:248px"><span class="word">HELIX</span><span class="sub">NEURO-DIAGNOSTICS</span></div>
</section>

<!-- Cover: white with blue band -->
<section class="slide col-1 row-3">
  <svg class="bg" viewBox="0 0 367 274" preserveAspectRatio="none" aria-hidden="true">
    <defs>
      <linearGradient id="stripe-a" x1="0" y1="0" x2="1" y2="0"><stop offset="0" stop-color="var(--navy)"/><stop offset="1" stop-color="var(--glow)"/></linearGradient>
    </defs>
    <polygon points="318,0 367,0 367,65" fill="var(--sky)"/>
    <polygon points="0,103 0,170 50,170" fill="var(--ice)"/>
    <rect y="170" width="367" height="104" fill="var(--azure)"/>
    <polygon points="50,170 140,170 240,274 150,274" fill="url(#stripe-a)"/>
  </svg>
  <div class="brand cover blue" style="top:98px"><span class="word">HELIX</span><span class="sub">NEURO-DIAGNOSTICS</span></div>
</section>

<!-- Divider: white with blue band -->
<section class="slide col-2 row-3">
  <svg class="bg" viewBox="0 0 367 274" preserveAspectRatio="none" aria-hidden="true">
    <defs>
      <linearGradient id="stripe-b" x1="0" y1="0" x2="1" y2="0"><stop offset="0" stop-color="var(--navy)"/><stop offset="1" stop-color="var(--glow)"/></linearGradient>
    </defs>
    <polygon points="0,50 0,115 50,115" fill="var(--ice)"/>
    <rect y="115" width="367" height="106" fill="var(--azure)"/>
    <polygon points="50,115 140,115 240,221 150,221" fill="url(#stripe-b)"/>
  </svg>
  <h2 class="heading blue" style="top:64px">DIVIDER PAGE HERE<span class="subtitle">SUBTITLE HERE</span></h2>
</section>

<!-- Closeout: white with blue band -->
<section class="slide col-3 row-3">
  <svg class="bg" viewBox="0 0 367 274" preserveAspectRatio="none" aria-hidden="true">
    <defs>
      <linearGradient id="stripe-c" x1="0" y1="0" x2="1" y2="0"><stop offset="0" stop-color="var(--navy)"/><stop offset="1" stop-color="var(--glow)"/></linearGradient>
    </defs>
    <polygon points="318,0 367,0 367,65" fill="var(--sky)"/>
    <polygon points="0,103 0,170 50,170" fill="var(--ice)"/>
    <rect y="170" width="367" height="104" fill="var(--azure)"/>
    <polygon points="50,170 140,170 240,274 150,274" fill="url(#stripe-c)"/>
  </svg>
  <div class="brand mini" style="left:15px;top:197px"><span class="word">HELIX</span><span class="sub">NEURO-DIAGNOSTICS</span></div>
  <address class="contact" style="left:15px;top:225px">
    <div class="url">http://helixneuro.net/</div>
    <div>admin@helixneuro.com</div>
    <div>1480 Larkspur Lane, Cedar Hollow, TX 75112</div>
  </address>
</section>

</body>
</html>
```